Agriculture Security Company needs a business card design

We need a business card design for a new company based in Seattle calls Ferncrest Guardline LLC. We provide high-end physical security solutions that is geared and focused towards to the marijuana grow operations, wholesalers and distributors. We DO NOT get involved in the retail operations (store fronts). We would like to see designs that incorporate professionalism, reliability, trustworthy and forward thinking as traits of our organization.

Industry/Entity Type

Security

```html
<!DOCTYPE html>
<html lang="en">
<head>
<meta charset="utf-8">
<title>Ferncrest Guardline LLC — Business Card</title>
<link rel="stylesheet" href="https://fonts.googleapis.com/css2?family=Cinzel:wght@700&family=Open+Sans:wght@400;600&display=swap">
<style>
  :root {
    --bg: #e9e6df;
    --card: #ffffff;
    --green-dark: #1f7a3a;
    --green-mid: #3f9a3c;
    --green-light: #8dbf3f;
    --sky: #5d9bd5;
    --ink: #3b3b3b;
    --shadow: rgba(0,0,0,0.18);
  }
  * { margin: 0; padding: 0; box-sizing: border-box; }
  html, body { width: 1200px; height: 1023px; overflow: hidden; }
  body { background: var(--bg); font-family: "Open Sans", sans-serif; position: relative; }

  .card {
    position: absolute;
    background: var(--card);
    border-radius: 18px;
    overflow: hidden;
    box-shadow: 0 10px 28px var(--shadow);
  }
  .card--front { left: 60px; top: 130px; width: 620px; height: 354px; }
  .card--back  { left: 540px; top: 540px; width: 600px; height: 342px;
                 background: linear-gradient(160deg, #ffffff, #f1f1f1); }

  .card__bands { position: absolute; inset: 0; }

  .brand {
    position: absolute;
    font-family: "Cinzel", serif;
    font-weight: 700;
    color: var(--green-dark);
    line-height: 1.05;
    letter-spacing: 1px;
  }
  .card--front .brand { left: 50px; top: 120px; font-size: 34px; }
  .brand__llc { display: block; font-size: 16px; letter-spacing: 3px; margin-top: 4px; }

  .divider {
    position: absolute; left: 318px; top: 108px; width: 2px; height: 130px;
    background: linear-gradient(var(--card), var(--green-mid), var(--card));
  }

  .contact { position: absolute; left: 340px; top: 118px; list-style: none; }
  .contact li {
    display: flex; align-items: center; gap: 10px;
    font-size: 15px; color: var(--ink); margin-bottom: 14px;
  }
  .contact svg { width: 16px; height: 16px; flex: none; }

  .person { position: absolute; left: 340px; top: 250px; }
  .person__name { font-size: 22px; font-weight: 600; color: var(--green-dark); }
  .person__title { font-size: 14px; color: var(--green-light); }

  .card--back .brand {
    left: 100px; right: 30px; top: 50%;
    transform: translateY(-50%);
    text-align: center; font-size: 36px;
  }
  .card--back .brand__llc { font-size: 16px; margin-top: 8px; }

  .back-url {
    position: absolute; left: 30px; top: 50%;
    transform: translateY(-50%);
    writing-mode: vertical-rl;
    font-size: 14px; letter-spacing: 3px; color: var(--green-dark);
    white-space: nowrap;
  }
</style>
</head>
<body>

<section class="card card--front" aria-label="Business card front">
  <svg class="card__bands" viewBox="0 0 620 354" preserveAspectRatio="none" aria-hidden="true">
    <path d="M0 0 H620 V60 Q320 -10 0 28 Z" fill="var(--green-mid)"/>
    <path d="M0 28 Q320 -10 620 60" fill="none" stroke="var(--sky)" stroke-width="7"/>
    <path d="M0 38 Q320 2 620 70" fill="none" stroke="#ffffff" stroke-width="5"/>
    <path d="M0 354 H620 V320 Q300 350 0 296 Z" fill="var(--green-light)"/>
    <path d="M0 296 Q300 350 620 320" fill="none" stroke="var(--sky)" stroke-width="7"/>
    <path d="M0 286 Q300 340 620 310" fill="none" stroke="#ffffff" stroke-width="5"/>
  </svg>

  <div class="brand">Ferncrest<br>Guardline<span class="brand__llc">LLC</span></div>

  <div class="divider"></div>

  <ul class="contact">
    <li>
      <svg viewBox="0 0 24 24"><path fill="var(--green-dark)" d="M6.6 10.8a15 15 0 0 0 6.6 6.6l2.2-2.2a1 1 0 0 1 1-.25 11.4 11.4 0 0 0 3.6.57 1 1 0 0 1 1 1V20a1 1 0 0 1-1 1A17 17 0 0 1 3 4a1 1 0 0 1 1-1h3.5a1 1 0 0 1 1 1c0 1.25.2 2.45.57 3.6a1 1 0 0 1-.25 1z"/></svg>
      555-014-2290
    </li>
    <li>
      <svg viewBox="0 0 24 24"><rect x="2" y="5" width="20" height="14" rx="2" fill="var(--green-dark)"/><path d="M3 6l9 7 9-7" fill="none" stroke="#fff" stroke-width="1.6"/></svg>
      info@ferncrestguardline.com
    </li>
    <li>
      <svg viewBox="0 0 24 24"><circle cx="12" cy="12" r="10" fill="var(--green-dark)"/><path d="M2 12h20M12 2c3 3 3 17 0 20M12 2c-3 3-3 17 0 20" fill="none" stroke="#fff" stroke-width="1.3"/></svg>
      www.ferncrestguardline.com
    </li>
  </ul>

  <div class="person">
    <div class="person__name">Dana Whitfield</div>
    <div class="person__title">President</div>
  </div>
</section>

<section class="card card--back" aria-label="Business card back">
  <div class="back-url">www.ferncrestguardline.com</div>
  <div class="brand">Ferncrest Guardline<span class="brand__llc">LLC</span></div>
</section>

</body>
</html>
```